Job Recruiting Agemcy

almost like my current site www.plorvex.com but with these changes see and what i meant about the across the to the site says home job companies categories pages blog and login sign up that should only be the 4 i said only 1 home 2 industries 3 jobs 4 contact us. and remove latest blog post and our partners because that's not us we have to post acuarte information thanks and the name of the company if your using is is work and careful hiring partners and want it easy for us to post and remove jobs and where it emails us every resume or person that applies

Requirements
Must have
• must send email to us when an application is submitted and try to incorparate the colors of current site
Nice to have
• i want a pretty basic site for now just like the one i have but with all thats above were its easy for me being the own to be able to post jobs and everything

```html
<!DOCTYPE html>
<html lang="en">
<head>
<meta charset="utf-8">
<title>WCHP – Recruiting Home Page Colour Options</title>
<link href="https://fonts.googleapis.com/css2?family=Lato:wght@400;700&family=Poppins:wght@700;800&display=swap" rel="stylesheet">
<style>
  :root{
    --canvas:#ffffff;
    --light:#f0f0f0;
    --ink:#1e1e1e;
    --muted:#6b6b6b;
    --footer:#000000;
    --white:#ffffff;
  }
  .theme-red{ --accent:#d6404f; --band:#9d3349; --card:#d64652; --icon-a:#d2248f; --icon-b:#6b1fd6; --icon-line:#ffffff; }
  .theme-green{ --accent:#2d5e43; --band:#2b5640; --card:#2f6444; --icon-a:#efefef; --icon-b:#e2e2e2; --icon-line:#2d5e43; }

  html,body{margin:0;padding:0;}
  body{width:1180px;height:1200px;overflow:hidden;background:var(--canvas);position:relative;font-family:'Lato',sans-serif;color:var(--ink);}

  .page{position:absolute;top:30px;width:904px;height:1838px;transform:scale(0.6195);transform-origin:0 0;overflow:hidden;}
  .page-left{left:17px;}
  .page-right{left:603px;}

  section,header,footer{position:absolute;left:0;width:904px;}
  .abs{position:absolute;}

  /* hero */
  .hero{top:0;height:452px;background:var(--light);}
  .hero-photo{position:absolute;right:0;top:0;width:430px;height:452px;
    background:
      radial-gradient(ellipse 90px 120px at 330px 120px,rgba(60,52,48,.55),rgba(60,52,48,0)),
      radial-gradient(ellipse 110px 140px at 220px 300px,rgba(70,78,96,.55),rgba(70,78,96,0)),
      radial-gradient(ellipse 120px 90px at 360px 380px,rgba(184,150,120,.6),rgba(184,150,120,0)),
      radial-gradient(ellipse 140px 200px at 120px 220px,rgba(255,255,255,.7),rgba(255,255,255,0)),
      linear-gradient(100deg,#ececec 0%,#e2dfdc 30%,#bdb7b1 60%,#7a726c 85%,#8d857e 100%);}
  .hero-fade{position:absolute;left:330px;top:0;width:200px;height:452px;background:linear-gradient(90deg,var(--light),rgba(240,240,240,0));}
  .brand{left:85px;top:22px;display:flex;flex-direction:column;align-items:center;gap:6px;}
  .brand-mark{width:26px;height:26px;border-radius:50%;background:var(--accent);}
  .brand-name{font-weight:700;font-size:12px;color:var(--accent);letter-spacing:.5px;}
  .nav{top:48px;left:352px;display:flex;gap:41px;font-size:12px;letter-spacing:.2px;}
  .nav a{color:var(--ink);text-decoration:none;}
  .nav a.active{color:var(--accent);}
  .btn-signup{left:712px;top:38px;width:106px;height:32px;border:1.5px solid #222;border-radius:3px;box-sizing:border-box;font-size:12px;display:flex;align-items:center;justify-content:center;background:rgba(255,255,255,.15);}
  .hero-title{left:84px;top:158px;margin:0;font-family:'Poppins',sans-serif;font-weight:800;font-size:31px;letter-spacing:.3px;color:var(--ink);}
  .hero-text{left:84px;top:213px;width:410px;margin:0;font-size:12px;line-height:21px;}
  .field{top:278px;width:167px;height:33px;border:1px solid #555;border-radius:3px;box-sizing:border-box;display:flex;align-items:center;gap:12px;padding-left:12px;font-size:12px;}
  .btn{display:flex;align-items:center;justify-content:center;font-size:12px;border-radius:3px;}
  .btn-solid{background:var(--accent);color:var(--white);}
  .btn-light{background:var(--white);color:#444;}

  /* about */
  .about{top:452px;height:308px;background:var(--light);text-align:center;}
  .section-title{margin:0;font-family:'Poppins',sans-serif;font-weight:800;font-size:23px;color:var(--accent);text-align:center;width:904px;}
  .about-text{left:154px;top:104px;width:596px;margin:0;font-size:11.4px;line-height:21.3px;color:#444;text-align:justify;text-align-last:center;}

  /* industries */
  .industries{top:760px;height:298px;background:var(--white);}
  .industries-intro{top:97px;left:150px;width:604px;margin:0;text-align:center;font-size:14px;line-height:18px;}
  .industry{top:158px;display:flex;gap:18px;}
  .industry-icon{width:58px;height:58px;flex:none;border-radius:3px;background:linear-gradient(135deg,var(--icon-a),var(--icon-b));display:flex;align-items:center;justify-content:center;}
  .industry h3{margin:0 0 8px;font-weight:400;font-size:14px;color:var(--ink);white-space:nowrap;}
  .industry p{margin:0;font-size:11.5px;line-height:18px;color:var(--muted);white-space:nowrap;}

  /* seeking */
  .seeking{top:1058px;height:237px;background:var(--band);color:var(--white);text-align:center;}
  .seeking h2{position:absolute;top:62px;width:904px;margin:0;font-family:'Poppins',sans-serif;font-weight:800;font-size:22px;}
  .seeking p{position:absolute;top:102px;width:904px;margin:0;font-size:14px;}

  /* testimonials */
  .testimonials{top:1295px;height:355px;background:var(--white);}
  .quote-card{top:102px;width:235px;height:127px;background:var(--white);box-shadow:0 0 6px rgba(0,0,0,.1);box-sizing:border-box;padding:19px 13px 0;font-size:10.2px;line-height:18px;color:#555;text-align:center;}
  .quote-card.featured{background:var(--card);color:var(--white);box-shadow:none;}
  .avatar{top:207px;width:45px;height:45px;background:radial-gradient(circle at 50% 40%,#d8c2b2 0 30%,rgba(216,194,178,0) 31%),linear-gradient(180deg,#e6e4e2 0%,#b9b1aa 60%,#5f6a7a 100%);}
  .person{top:262px;width:235px;text-align:center;font-size:10px;line-height:19px;color:#222;}

  /* footer */
  .site-footer{top:1650px;height:188px;background:var(--footer);color:var(--white);}
  .footer-nav{top:62px;left:0;width:904px;display:flex;justify-content:center;gap:31px;font-size:15.5px;font-weight:700;transform:translateX(-20px);}
  .copyright{top:96px;width:904px;text-align:center;font-size:16px;margin:0;transform:translateX(-20px);}
  .social{top:135px;width:28px;height:28px;border:1.5px solid var(--white);border-radius:50%;box-sizing:border-box;}
</style>
</head>
<body>

<main class="page page-left theme-red">
  <header class="hero">
    <div class="hero-photo" role="img" aria-label="Photo of a recruiting team meeting around a white office table with laptops"></div>
    <div class="hero-fade"></div>
    <div class="abs brand"><span class="brand-mark"></span><span class="brand-name">WCHP</span></div>
    <nav class="abs nav"><a class="active">HOME</a><a>INDUSTRIES</a><a>JOBS</a><a>CONTACT US</a></nav>
    <div class="abs btn-signup">SIGN UP</div>
    <h1 class="abs hero-title">YOUR CAREER STARTS HERE!</h1>
    <p class="abs hero-text">We have over 35 years of Specialized Recruiting and souring experience. We cover a broad spectrum of industries to include.</p>
    <div class="abs field" style="left:84px"><svg width="11" height="11" viewBox="0 0 11 11"><circle cx="4.5" cy="4.5" r="3.3" fill="none" stroke="#222" stroke-width="1.6"/><line x1="7" y1="7" x2="10" y2="10" stroke="#222" stroke-width="1.8"/></svg>Keywords</div>
    <div class="abs field" style="left:264px"><svg width="9" height="12" viewBox="0 0 9 12"><path d="M4.5 0.5a4 4 0 0 1 4 4c0 3-4 7-4 7s-4-4-4-7a4 4 0 0 1 4-4z" fill="#222"/><circle cx="4.5" cy="4.5" r="1.4" fill="#fff"/></svg>Location</div>
    <div class="abs btn btn-solid" style="left:84px;top:340px;width:109px;height:32px">Search</div>
  </header>

  <section class="about">
    <h2 class="abs section-title" style="top:59px">ABOUT US</h2>
    <p class="abs about-text">Maecenas mollis dictum lectus quis scelerisque. Nulla at rutrum ipsum. Praesent augue quam, facilisis vitae felis vel, convallis convallis nisi. Donec maximus accumsan purus vel tempus. Aenean pretium luctus velit id fermentum. Aenean non velit non nulla interdum venenatis. Integer in libero sagittis, consequat est quis, commodo odio. Aliquam eu vulputate neque. Nunc et massa leo. Vestibulum a pretium dolor.</p>
    <div class="abs btn btn-solid" style="left:407px;top:211px;width:109px;height:32px">Read More</div>
  </section>

  <section class="industries">
    <h2 class="abs section-title" style="top:57px">INDUSTRIES WE SUPPORT</h2>
    <p class="abs industries-intro">Lorem ipsum dolor sit amet, consectetur adipiscing elit, sed do eiusmod tempor incididunt ut labore et dolore magna aliqua.</p>
    <div class="abs industry" style="left:84px"><div class="industry-icon" role="img" aria-label="Aerospace worker icon"></div><div><h3>Aero Space</h3><p>Orvane Aero<br>Controls, Zentro<br>Velkor Electric</p></div></div>
    <div class="abs industry" style="left:280px"><div class="industry-icon" role="img" aria-label="Pharmaceutical worker icon"></div><div><h3>Pharmaceutical</h3><p>Biovance Life<br>Tech , Lumora<br>cosmetics</p></div></div>
    <div class="abs industry" style="left:491px"><div class="industry-icon"><svg width="42" height="30" viewBox="0 0 42 30" fill="none" stroke="var(--icon-line)" stroke-width="1.6" stroke-linejoin="round"><rect x="2" y="4" width="24" height="18"/><path d="M26 10h8l6 7v5H26z"/><circle cx="9" cy="24" r="3.2" fill="var(--icon-b)"/><circle cx="33" cy="24" r="3.2" fill="var(--icon-b)"/><line x1="5" y1="9" x2="15" y2="9"/></svg></div><div><h3>Transportation</h3><p>Brantley Trucking,<br>Parcelon</p></div></div>
    <div class="abs industry" style="left:694px"><div class="industry-icon" role="img" aria-label="Doctor icon"></div><div><h3>Medical</h3><p>Medira,<br>Cliniq</p></div></div>
  </section>

  <section class="seeking">
    <h2>SEEKING FOR A JOB?</h2>
    <p>Browse hundreds of job offers and find the best suitable position.</p>
    <div class="abs btn btn-light" style="left:343px;top:140px;width:101px;height:31px">Search Jobs</div>
    <div class="abs btn btn-light" style="left:460px;top:140px;width:101px;height:31px">Add a Resume</div>
  </section>

  <section class="testimonials">
    <h2 class="abs section-title" style="top:57px">TESTIMONIALS</h2>
    <div class="abs quote-card" style="left:84px">“I was highly impressed by the<br>professionalism shown during my interview process. It was less an interview and more of a conversation with the recruiter.”</div>
    <div class="abs quote-card featured" style="left:334px">“I was highly impressed by the<br>professionalism shown during my interview process. It was less an interview and more of a conversation with the recruiter.”</div>
    <div class="abs quote-card" style="left:584px">“I was highly impressed by the<br>professionalism shown during my interview process. It was less an interview and more of a conversation with the recruiter.”</div>
    <div class="abs avatar" style="left:179px" role="img" aria-label="Portrait photo of Marla Quint"></div>
    <div class="abs avatar" style="left:429px" role="img" aria-label="Portrait photo of Tobin Harlow"></div>
    <div class="abs avatar" style="left:679px" role="img" aria-label="Portrait photo of Delia Vance"></div>
    <div class="abs person" style="left:84px">Marla Quint<br>CEO in Company Name</div>
    <div class="abs person" style="left:334px">Tobin Harlow<br>Key Account Manager in Chirpwell Inc.</div>
    <div class="abs person" style="left:584px">Delia Vance<br>HR Manager in Orchardly Inc.</div>
  </section>

  <footer class="site-footer">
    <nav class="abs footer-nav"><span>HOME</span><span>INDUSTRIES</span><span>JOBS</span><span>TESTIMONIALS</span><span>CONTACT US</span></nav>
    <p class="abs copyright">2020 WCHP Pvt Ltd.&nbsp; All rights reserved</p>
    <span class="abs social" style="left:410px"></span>
    <span class="abs social" style="left:449px"></span>
    <span class="abs social" style="left:488px"></span>
  </footer>
</main>

<main class="page page-right theme-green">
  <header class="hero">
    <div class="hero-photo" role="img" aria-label="Photo of a recruiting team meeting around a white office table with laptops"></div>
    <div class="hero-fade"></div>
    <div class="abs brand"><span class="brand-mark"></span><span class="brand-name">WCHP</span></div>
    <nav class="abs nav"><a class="active">HOME</a><a>INDUSTRIES</a><a>JOBS</a><a>CONTACT US</a></nav>
    <div class="abs btn-signup">SIGN UP</div>
    <h1 class="abs hero-title">YOUR CAREER STARTS HERE!</h1>
    <p class="abs hero-text">We have over 35 years of Specialized Recruiting and souring experience. We cover a broad spectrum of industries to include.</p>
    <div class="abs field" style="left:84px"><svg width="11" height="11" viewBox="0 0 11 11"><circle cx="4.5" cy="4.5" r="3.3" fill="none" stroke="#222" stroke-width="1.6"/><line x1="7" y1="7" x2="10" y2="10" stroke="#222" stroke-width="1.8"/></svg>Keywords</div>
    <div class="abs field" style="left:264px"><svg width="9" height="12" viewBox="0 0 9 12"><path d="M4.5 0.5a4 4 0 0 1 4 4c0 3-4 7-4 7s-4-4-4-7a4 4 0 0 1 4-4z" fill="#222"/><circle cx="4.5" cy="4.5" r="1.4" fill="#fff"/></svg>Location</div>
    <div class="abs btn btn-solid" style="left:84px;top:340px;width:109px;height:32px">Search</div>
  </header>

  <section class="about">
    <h2 class="abs section-title" style="top:59px">ABOUT US</h2>
    <p class="abs about-text">Maecenas mollis dictum lectus quis scelerisque. Nulla at rutrum ipsum. Praesent augue quam, facilisis vitae felis vel, convallis convallis nisi. Donec maximus accumsan purus vel tempus. Aenean pretium luctus velit id fermentum. Aenean non velit non nulla interdum venenatis. Integer in libero sagittis, consequat est quis, commodo odio. Aliquam eu vulputate neque. Nunc et massa leo. Vestibulum a pretium dolor.</p>
    <div class="abs btn btn-solid" style="left:407px;top:211px;width:109px;height:32px">Read More</div>
  </section>

  <section class="industries">
    <h2 class="abs section-title" style="top:57px">INDUSTRIES WE SUPPORT</h2>
    <p class="abs industries-intro">Lorem ipsum dolor sit amet, consectetur adipiscing elit, sed do eiusmod tempor incididunt ut labore et dolore magna aliqua.</p>
    <div class="abs industry" style="left:84px"><div class="industry-icon" role="img" aria-label="Aerospace worker icon"></div><div><h3>Aero Space</h3><p>Orvane Aero<br>Controls, Zentro<br>Velkor Electric</p></div></div>
    <div class="abs industry" style="left:280px"><div class="industry-icon" role="img" aria-label="Pharmaceutical worker icon"></div><div><h3>Pharmaceutical</h3><p>Biovance Life<br>Tech , Lumora<br>cosmetics</p></div></div>
    <div class="abs industry" style="left:491px"><div class="industry-icon"><svg width="42" height="30" viewBox="0 0 42 30" fill="none" stroke="var(--icon-line)" stroke-width="1.6" stroke-linejoin="round"><rect x="2" y="4" width="24" height="18"/><path d="M26 10h8l6 7v5H26z"/><circle cx="9" cy="24" r="3.2" fill="var(--icon-b)"/><circle cx="33" cy="24" r="3.2" fill="var(--icon-b)"/><line x1="5" y1="9" x2="15" y2="9"/></svg></div><div><h3>Transportation</h3><p>Brantley Trucking,<br>Parcelon</p></div></div>
    <div class="abs industry" style="left:694px"><div class="industry-icon" role="img" aria-label="Doctor icon"></div><div><h3>Medical</h3><p>Medira,<br>Cliniq</p></div></div>
  </section>

  <section class="seeking">
    <h2>SEEKING FOR A JOB?</h2>
    <p>Browse hundreds of job offers and find the best suitable position.</p>
    <div class="abs btn btn-light" style="left:343px;top:140px;width:101px;height:31px">Search Jobs</div>
    <div class="abs btn btn-light" style="left:460px;top:140px;width:101px;height:31px">Add a Resume</div>
  </section>

  <section class="testimonials">
    <h2 class="abs section-title" style="top:57px">TESTIMONIALS</h2>
    <div class="abs quote-card" style="left:84px">“I was highly impressed by the<br>professionalism shown during my interview process. It was less an interview and more of a conversation with the recruiter.”</div>
    <div class="abs quote-card featured" style="left:334px">“I was highly impressed by the<br>professionalism shown during my interview process. It was less an interview and more of a conversation with the recruiter.”</div>
    <div class="abs quote-card" style="left:584px">“I was highly impressed by the<br>professionalism shown during my interview process. It was less an interview and more of a conversation with the recruiter.”</div>
    <div class="abs avatar" style="left:179px" role="img" aria-label="Portrait photo of Marla Quint"></div>
    <div class="abs avatar" style="left:429px" role="img" aria-label="Portrait photo of Tobin Harlow"></div>
    <div class="abs avatar" style="left:679px" role="img" aria-label="Portrait photo of Delia Vance"></div>
    <div class="abs person" style="left:84px">Marla Quint<br>CEO in Company Name</div>
    <div class="abs person" style="left:334px">Tobin Harlow<br>Key Account Manager in Chirpwell Inc.</div>
    <div class="abs person" style="left:584px">Delia Vance<br>HR Manager in Orchardly Inc.</div>
  </section>

  <footer class="site-footer">
    <nav class="abs footer-nav"><span>HOME</span><span>INDUSTRIES</span><span>JOBS</span><span>TESTIMONIALS</span><span>CONTACT US</span></nav>
    <p class="abs copyright">2020 WCHP Pvt Ltd.&nbsp; All rights reserved</p>
    <span class="abs social" style="left:410px"></span>
    <span class="abs social" style="left:449px"></span>
    <span class="abs social" style="left:488px"></span>
  </footer>
</main>

</body>
</html>
```